New Business Card for Software Company

We are looking at rebranding a 10 year old company that specializes in PDF and DWF solutions for Architects and Engineers. We will attach the new company logo that we are going with so you can work with that and complimentary colors.
The sample information we would like on the business card is:
Gerald Pinfold
Vice President
4738 W. Harrowgate Lane. STE 305
PMB#417
Tarrowbend, AZ 85374
866-392-5074 US Toll Free
123-456-3190 Cell
gpinfold@plavorix.com
The old tag line that we had on the business cars was.
Delivering Dependable Document and Drawing Tools to Design Teams Around the World.
If you have an idea for a better tag line we are open to that also.
Updates
We would like to thank all of the Designers for their wonderful work. We apologize that we will not have the time to provide feedback to everyone. There is just so many innovative and professional designs that you have all created making our decision even harder.
Target Market(s)
Architects and Engineers
Industry/Entity Type
Business
Look and feel

```html
<!DOCTYPE html>
<html lang="en">
<head>
<meta charset="utf-8">
<title>Plavorix Business Card</title>
<link rel="stylesheet" href="https://fonts.googleapis.com/css2?family=Open+Sans:wght@400;600;700;800&display=swap">
<style>
  :root {
    --bg: #e9e6e2;
    --card-dark: #2b2b2d;
    --card-dark-deep: #1c1c1e;
    --card-light: #ffffff;
    --brand-orange: #f07a1e;
    --accent-gold: #f5b335;
    --text-light: #e8e8e8;
  }
  * { margin: 0; padding: 0; box-sizing: border-box; }
  html, body { width: 850px; height: 1200px; overflow: hidden; }
  body {
    background: var(--bg);
    font-family: "Open Sans", Arial, sans-serif;
    position: relative;
  }
  .card {
    position: absolute;
    left: 75px;
    width: 700px;
    height: 400px;
    border-radius: 4px;
    overflow: hidden;
    box-shadow: 0 10px 28px rgba(0,0,0,0.25);
  }
  .card-front { top: 150px; background: var(--card-light); }
  .card-back {
    top: 650px;
    background: linear-gradient(135deg, var(--card-dark) 0%, var(--card-dark-deep) 100%);
  }
  .card-shape { position: absolute; inset: 0; }
  .brand {
    position: absolute;
    display: flex;
    align-items: center;
    gap: 14px;
  }
  .brand-dot {
    width: 52px; height: 52px;
    border-radius: 50%;
    background: var(--brand-orange);
  }
  .brand-name {
    font-weight: 800;
    font-size: 60px;
    letter-spacing: -1px;
    color: var(--brand-orange);
    line-height: 1;
  }
  .card-front .brand { left: 48px; top: 44px; }
  .contact-list {
    position: absolute;
    left: 48px; top: 262px;
    list-style: none;
    color: var(--text-light);
    font-size: 15px;
    line-height: 26px;
  }
  .contact-list li { display: flex; align-items: center; gap: 9px; }
  .contact-icon { width: 12px; height: 12px; flex: none; }
  .person {
    position: absolute;
    right: 44px; top: 250px;
    text-align: right;
    color: var(--text-light);
  }
  .person-name { font-size: 26px; font-weight: 400; line-height: 1.1; }
  .person-title { font-size: 17px; color: var(--brand-orange); margin-bottom: 12px; }
  .person-address { font-size: 15px; line-height: 21px; font-style: normal; }

  .back-grid { position: absolute; inset: 0; }
  .card-back .brand { left: 190px; top: 130px; }
  .card-back .brand-name { color: #ffffff; font-size: 68px; }
  .card-back .brand-dot { width: 60px; height: 60px; }
  .tagline {
    position: absolute;
    left: 60px; right: 60px; top: 228px;
    color: var(--text-light);
    font-size: 19px;
    line-height: 28px;
    text-align: center;
  }
</style>
</head>
<body>

  <section class="card card-front" aria-label="Business card front">
    <svg class="card-shape" viewBox="0 0 700 400" preserveAspectRatio="none">
      <path d="M0 205 Q330 150 700 232 L700 400 L0 400 Z" fill="var(--card-dark)"/>
      <path d="M230 170 Q470 175 700 226" fill="none" stroke="var(--accent-gold)" stroke-width="5"/>
      <path d="M150 176 Q420 168 700 232" fill="none" stroke="var(--brand-orange)" stroke-width="2"/>
    </svg>

    <div class="brand">
      <span class="brand-dot"></span>
      <span class="brand-name">Plavorix</span>
    </div>

    <ul class="contact-list">
      <li>
        <svg class="contact-icon" viewBox="0 0 12 12"><path d="M2 1 L4.5 1 L5.3 3.6 L3.8 4.6 Q5 7.2 7.4 8.2 L8.4 6.7 L11 7.5 L11 10 Q5.5 11 1.5 4 Z" fill="var(--brand-orange)"/></svg>
        866-392-5074 US Toll Free
      </li>
      <li>
        <svg class="contact-icon" viewBox="0 0 12 12"><rect x="3" y="0.5" width="6" height="11" rx="1.2" fill="none" stroke="var(--brand-orange)" stroke-width="1.4"/></svg>
        123-456-3190
      </li>
      <li>
        <svg class="contact-icon" viewBox="0 0 12 12"><circle cx="6" cy="6" r="5.3" fill="var(--brand-orange)"/><circle cx="6" cy="6" r="2" fill="var(--card-dark)"/></svg>
        gpinfold@plavorix.com
      </li>
    </ul>

    <div class="person">
      <p class="person-name">Gerald Pinfold</p>
      <p class="person-title">Vice President</p>
      <address class="person-address">
        4738 W. Harrowgate Lane. STE 305<br>
        PMB#417<br>
        Tarrowbend, AZ 85374
      </address>
    </div>
  </section>

  <section class="card card-back" aria-label="Business card back">
    <div class="back-grid" role="img" aria-label="Faint curved wireframe grid texture"
         style="background: radial-gradient(ellipse at 75% 30%, rgba(255,255,255,0.07) 0%, rgba(255,255,255,0) 60%);"></div>

    <div class="brand">
      <span class="brand-dot"></span>
      <span class="brand-name">Plavorix</span>
    </div>

    <p class="tagline">Delivering Dependable Document and Drawing<br>Tools to Design Teams Around the World</p>
  </section>

</body>
</html>
```